Step and Repeat Backdrop for wedding reception photo booth

Would like to have a Step and Repeat Backdrop (8 foot high by 10 foot wide) that incorporates the wedding logo (attached) and the names Helen and Gavin. Background should be white, and wedding colors are burgundy and gold. Show me creativity :-) I have included some random samples.

```html
<!DOCTYPE html>
<html lang="en">
<head>
<meta charset="utf-8">
<title>Helen &amp; Gavin — Step and Repeat Backdrop</title>
<link href="https://fonts.googleapis.com/css2?family=Cormorant+Garamond:wght@500;600&display=swap" rel="stylesheet">
<style>
  :root {
    --page: #ffffff;
    --burgundy: #8c1535;
    --tile-ink: #a8485e;
    --tile-flourish: rgba(196, 110, 120, 0.45);
    --gold: #eebf2e;
    --gold-soft: #f3d35a;
    --gold-deep: #d9a21e;
  }
  * { box-sizing: border-box; margin: 0; padding: 0; }
  html, body {
    width: 1200px; height: 1200px; overflow: hidden;
    background: var(--page);
  }
  .canvas { position: relative; width: 1200px; height: 1200px; }

  .backdrop {
    position: absolute; left: 50px; top: 153px;
    width: 1100px; height: 893px;
    background: var(--burgundy);
    overflow: hidden;
  }

  .repeat-grid {
    position: absolute; inset: 0;
    display: grid;
    grid-template-columns: repeat(8, 137.5px);
    grid-template-rows: repeat(8, 106px);
    padding: 23px 0 0 2px;
  }
  .tile {
    display: flex; flex-direction: column; align-items: center; justify-content: center;
    gap: 4px;
    font-family: "Cormorant Garamond", serif;
    font-weight: 500; font-size: 42px; line-height: 0.9;
    color: var(--tile-ink);
    letter-spacing: -1px;
  }
  .tile::before, .tile::after {
    content: ""; display: block;
    width: 90px; height: 16px; border-radius: 8px;
    background: var(--tile-flourish);
  }
  .tile.is-covered { visibility: hidden; }

  .crest {
    position: absolute; left: 0; right: 0; top: 228px;
    display: flex; flex-direction: column; align-items: center;
  }
  .flourish {
    width: 310px; height: 94px; border-radius: 47px;
    background: radial-gradient(ellipse at center, var(--gold-soft) 0%, var(--gold) 45%, rgba(238,191,46,0.35) 100%);
  }
  .monogram {
    font-family: "Cormorant Garamond", serif;
    font-weight: 600; font-size: 150px; line-height: 1;
    color: var(--gold);
    letter-spacing: -4px;
    margin: 6px 0 4px;
  }

  .couple {
    position: absolute; left: 0; right: 0; top: 568px;
    display: flex; justify-content: center; align-items: center; gap: 14px;
    font-family: "Cormorant Garamond", serif;
    font-weight: 600; font-size: 44px;
    color: var(--gold);
    letter-spacing: 22px;
  }
  .couple .name:last-child { margin-right: -22px; }
  .rings {
    width: 54px; height: 58px; border-radius: 50%;
    background: radial-gradient(circle, var(--gold-soft), var(--gold-deep));
  }
</style>
</head>
<body>
<main class="canvas">
  <section class="backdrop" aria-label="Step and repeat backdrop for Helen and Gavin">
    <div class="repeat-grid" aria-hidden="true">
      <span class="tile">H&amp;G</span><span class="tile">H&amp;G</span><span class="tile">H&amp;G</span><span class="tile">H&amp;G</span><span class="tile">H&amp;G</span><span class="tile">H&amp;G</span><span class="tile">H&amp;G</span><span class="tile">H&amp;G</span>
      <span class="tile">H&amp;G</span><span class="tile">H&amp;G</span><span class="tile">H&amp;G</span><span class="tile">H&amp;G</span><span class="tile">H&amp;G</span><span class="tile">H&amp;G</span><span class="tile">H&amp;G</span><span class="tile">H&amp;G</span>
      <span class="tile">H&amp;G</span><span class="tile">H&amp;G</span><span class="tile">H&amp;G</span><span class="tile is-covered">H&amp;G</span><span class="tile is-covered">H&amp;G</span><span class="tile">H&amp;G</span><span class="tile">H&amp;G</span><span class="tile">H&amp;G</span>
      <span class="tile">H&amp;G</span><span class="tile">H&amp;G</span><span class="tile">H&amp;G</span><span class="tile is-covered">H&amp;G</span><span class="tile is-covered">H&amp;G</span><span class="tile">H&amp;G</span><span class="tile">H&amp;G</span><span class="tile">H&amp;G</span>
      <span class="tile">H&amp;G</span><span class="tile">H&amp;G</span><span class="tile">H&amp;G</span><span class="tile is-covered">H&amp;G</span><span class="tile is-covered">H&amp;G</span><span class="tile">H&amp;G</span><span class="tile">H&amp;G</span><span class="tile">H&amp;G</span>
      <span class="tile">H&amp;G</span><span class="tile">H&amp;G</span><span class="tile is-covered">H&amp;G</span><span class="tile is-covered">H&amp;G</span><span class="tile is-covered">H&amp;G</span><span class="tile is-covered">H&amp;G</span><span class="tile">H&amp;G</span><span class="tile">H&amp;G</span>
      <span class="tile">H&amp;G</span><span class="tile">H&amp;G</span><span class="tile">H&amp;G</span><span class="tile">H&amp;G</span><span class="tile">H&amp;G</span><span class="tile">H&amp;G</span><span class="tile">H&amp;G</span><span class="tile">H&amp;G</span>
      <span class="tile">H&amp;G</span><span class="tile">H&amp;G</span><span class="tile">H&amp;G</span><span class="tile">H&amp;G</span><span class="tile">H&amp;G</span><span class="tile">H&amp;G</span><span class="tile">H&amp;G</span><span class="tile">H&amp;G</span>
    </div>

    <div class="crest">
      <div class="flourish" role="img" aria-label="Gold scrollwork flourish above the monogram"></div>
      <h1 class="monogram">H&amp;G</h1>
      <div class="flourish" role="img" aria-label="Gold scrollwork flourish below the monogram"></div>
    </div>

    <p class="couple">
      <span class="name">Helen</span>
      <span class="rings" role="img" aria-label="Pair of gold wedding rings"></span>
      <span class="name">Gavin</span>
    </p>
  </section>
</main>
</body>
</html>
```